To design a brand identity that is simple and creative with 'Corvane' as the brand name, I like modern simple fonts like helvetica neue, I want to print both sides of the card, I am open to dark front and white back, but the design needs to transfer well to letter heads and email signatures, I am looking for sophisticated and elegant, but open minded about clever and off the wall, I do not do 'boring' Corvane Ventures is the mother company for a small group, specialising in Management & consulting, Software development and construction, we have a high level of integrity, we are transparent and accountable for what we do. my images are provided as a guide only, Im not expecting them to be just copied, Im looking for a creator and passionate thinker, who will put life into their work.

Target Market(s)

usually business minded people who are looking for something different in me, such as leadership, confidence and focus with thinking that is per haps a little outside the box..

Industry/Entity Type

Construction

Requirements
Must have
• clean, minmalistic
Nice to have
• custom logo
Should not have
• boring, traditional

```html
<!DOCTYPE html>
<html lang="en">
<head>
<meta charset="utf-8">
<title>Corvane Business Card</title>
<link href="https://fonts.googleapis.com/css2?family=Open+Sans:ital,wght@0,400;0,600;1,400&display=swap" rel="stylesheet">
<style>
  :root {
    --page-bg: #e6e6ea;
    --card-dark: #2b2b2c;
    --card-white: #ffffff;
    --accent-coral: #f0484f;
    --text-light: #ffffff;
    --text-muted: #9a9a9a;
    --text-dark: #333333;
    --stripe-taupe: #9c8a85;
    --band-yellow: #ffc400;
    --band-red: #ff1a1a;
    --band-purple: #7a2a6e;
    --band-teal: #10a88a;
    --bullet-grey: #a0a0a0;
  }
  * { box-sizing: border-box; margin: 0; padding: 0; }
  html, body { width: 1200px; height: 987px; overflow: hidden; }
  body {
    background: var(--page-bg);
    font-family: "Open Sans", "Helvetica Neue", Arial, sans-serif;
    position: relative;
  }
  .card {
    position: absolute;
    width: 540px;
    height: 310px;
    border-radius: 22px;
    overflow: hidden;
    box-shadow: 0 14px 30px rgba(0,0,0,0.18);
  }
  /* Front */
  .card-front { left: 40px; top: 338px; background: var(--card-dark); }
  .card-front .band { position: absolute; inset: 0; }
  .brand-lockup {
    position: absolute; left: 170px; top: 42px;
    display: flex; align-items: center; gap: 14px;
  }
  .brand-square {
    width: 22px; height: 22px;
    background: var(--accent-coral);
  }
  .brand-name {
    font-weight: 600; font-size: 50px; line-height: 1;
    letter-spacing: 2px;
    color: var(--text-light);
  }
  .tagline {
    position: absolute; left: 232px; top: 108px;
    font-style: italic; font-size: 15px; color: var(--text-muted);
  }
  .holder {
    position: absolute; left: 236px; top: 146px;
    color: var(--text-light); font-size: 19px; font-weight: 400;
  }
  .holder strong { font-weight: 600; }
  .contact {
    position: absolute; left: 26px; bottom: 20px;
    color: var(--text-light); font-size: 14px; line-height: 1.7;
    list-style: none;
  }
  .contact li { display: flex; align-items: center; gap: 8px; }
  .contact svg { width: 14px; height: 14px; flex: none; }
  /* Back */
  .card-back {
    left: 620px; top: 338px; background: var(--card-white);
    border: 1px solid #cfcfd4;
  }
  .back-lockup {
    position: absolute; right: 44px; top: 50px;
    display: flex; align-items: center; gap: 14px;
  }
  .back-lockup .brand-name { font-size: 46px; color: var(--text-dark); }
  .services {
    position: absolute; left: 40px; top: 158px;
    list-style: none; color: var(--accent-coral);
    font-size: 17px; line-height: 1.6;
  }
  .services li { display: inline-flex; align-items: center; gap: 7px; margin-right: 16px; }
  .services li::before {
    content: ""; width: 6px; height: 6px; border-radius: 50%;
    background: var(--bullet-grey);
  }
  .website {
    position: absolute; left: 40px; bottom: 40px;
    font-size: 20px; letter-spacing: 6px; color: var(--text-dark);
  }
</style>
</head>
<body>

<section class="card card-front" aria-label="Card front">
  <svg class="band" viewBox="0 0 540 310" preserveAspectRatio="none" aria-hidden="true">
    <defs>
      <linearGradient id="bandGradient" x1="0" y1="0" x2="1" y2="0">
        <stop offset="0" stop-color="var(--band-yellow)"/>
        <stop offset="0.3" stop-color="var(--band-red)"/>
        <stop offset="0.65" stop-color="var(--band-purple)"/>
        <stop offset="1" stop-color="var(--band-teal)"/>
      </linearGradient>
    </defs>
    <path d="M0,136 Q300,174 540,280 L540,310 L0,310 Z" fill="var(--stripe-taupe)"/>
    <path d="M0,150 Q300,190 540,292 L540,310 L0,310 Z" fill="url(#bandGradient)"/>
  </svg>

  <div class="brand-lockup">
    <span class="brand-square"></span>
    <span class="brand-name">CORVANE</span>
  </div>
  <p class="tagline">...in the creation business.</p>
  <p class="holder"><strong>Your Name,</strong> Title</p>

  <ul class="contact">
    <li>
      <svg viewBox="0 0 16 16"><circle cx="8" cy="8" r="7" fill="none" stroke="currentColor" stroke-width="1.4"/><path d="M5.5 4.5l1.5 1.5-1 1a5 5 0 0 0 3 3l1-1 1.5 1.5-1 1c-3 0-6-3-6-6z" fill="currentColor"/></svg>
      +61 0400 552 174
    </li>
    <li>
      <svg viewBox="0 0 16 16"><path d="M8 1a5 5 0 0 0-5 5c0 4 5 9 5 9s5-5 5-9a5 5 0 0 0-5-5zm0 7a2 2 0 1 1 0-4 2 2 0 0 1 0 4z" fill="currentColor"/></svg>
      Po Box 512 Perth 6000
    </li>
    <li>
      <svg viewBox="0 0 16 16"><rect x="1" y="3" width="14" height="10" rx="1.5" fill="currentColor"/><path d="M1.5 4l6.5 5 6.5-5" fill="none" stroke="var(--band-purple)" stroke-width="1.4"/></svg>
      names@corvane.ventures
    </li>
  </ul>
</section>

<section class="card card-back" aria-label="Card back">
  <div class="back-lockup">
    <span class="brand-square"></span>
    <span class="brand-name">CORVANE</span>
  </div>
  <ul class="services">
    <li>Management &amp; Consulting</li>
    <li>Software Development</li>
    <li>Construction</li>
  </ul>
  <p class="website">www.corvane.com</p>
</section>

</body>
</html>
```